Business Card Design For Office Furniture Clearance Company

Kestrel Office Clearance - our company name pretty much explains what we do, we clear offices for high end clients, mainly plc's and large international companies.

We require a nice looking business card that displays professionalism but without being too serious.

It would be nice to see just a little more than a conventional boring business card, make sure you add some flare.

Industry/Entity Type

Office Furniture

Contact Information for Business Card

CARD 1

Mark Holloway
Director
mark@kestrelofficeclearance.co.uk
m: 07700 153928

t: 01632 960418
www.kestrelofficeclearance.co.uk

Kestrel Office Clearance
Unit K4 B
2-8 Fenwick Lane
Harwick
Eastbury Vale
ZZ9 4QT

no-cost office clearing… simple, swift and tidy.

CARD 2

Peter Radford
Director
peter@kestrelofficeclearance.co.uk
m: 07700 382615

t: 01632 960418

Kestrel Office Clearance
Unit K4 B
2-8 Fenwick Lane
Harwick
Eastbury Vale
ZZ9 4QT

Font styles to use
Sans Serif

Requirements
Must have
• A white background - as we have a blue logo.
Nice to have
• Nice use of the logo - play around with this and dissect it.

```html
<!DOCTYPE html>
<html lang="en">
<head>
<meta charset="utf-8">
<title>Kestrel Office Clearance – Business Cards</title>
<link rel="stylesheet" href="https://fonts.googleapis.com/css2?family=Open+Sans:ital,wght@0,400;0,600;0,700;1,600&display=swap">
<style>
  :root {
    --brand-blue: #0a7bc1;
    --brand-blue-deep: #0a64a6;
    --band-navy: #0b5b96;
    --card-white: #ffffff;
    --stage: #eceef0;
    --ink-light: #ffffff;
  }
  * { box-sizing: border-box; margin: 0; padding: 0; }
  html, body { width: 1200px; height: 900px; overflow: hidden; }
  body {
    background: var(--stage);
    font-family: "Open Sans", Arial, sans-serif;
    position: relative;
  }
  .card { position: absolute; overflow: hidden; box-shadow: 0 4px 14px rgba(0,0,0,.18); }

  /* Front */
  .card-front { left: 78px; top: 35px; width: 588px; height: 363px; background: var(--card-white); }
  .card-front .shapes { position: absolute; inset: 0; }
  .brand-lockup {
    position: absolute; left: 0; right: 0; top: 70px;
    display: flex; align-items: center; justify-content: center; gap: 12px;
  }
  .brand-dot { width: 36px; height: 36px; border-radius: 50%; background: var(--brand-blue); }
  .brand-name { color: var(--brand-blue); font-weight: 700; font-size: 24px; }

  .contact-list {
    position: absolute; right: 294px; top: 226px;
    list-style: none; color: var(--ink-light); font-size: 15px; line-height: 25px; text-align: right;
  }
  .contact-list li { display: flex; justify-content: flex-end; align-items: center; gap: 9px; }
  .contact-list svg { width: 12px; height: 12px; flex: none; }

  .person { position: absolute; left: 321px; top: 200px; color: var(--ink-light); }
  .person-name { font-size: 21px; font-weight: 600; line-height: 28px; }
  .person-role { font-size: 15px; line-height: 20px; }
  .company-name { font-size: 19px; font-weight: 700; line-height: 26px; margin-top: 12px; }
  .address { font-style: normal; font-size: 15px; line-height: 21.5px; }

  /* Back */
  .card-back {
    left: 388px; top: 505px; width: 567px; height: 352px;
    background: linear-gradient(180deg, var(--brand-blue) 0%, var(--brand-blue-deep) 100%);
  }
  .back-lockup {
    position: absolute; left: 0; right: 0; top: 108px;
    display: flex; flex-direction: column; align-items: center; gap: 14px;
  }
  .back-dot { width: 96px; height: 96px; border-radius: 50%; background: var(--card-white); }
  .back-name { color: var(--ink-light); font-weight: 700; font-size: 22px; }
  .tagline {
    position: absolute; left: 0; right: 0; top: 288px;
    display: flex; align-items: center; gap: 8px;
    color: var(--ink-light); font-style: italic; font-weight: 600; font-size: 16.5px; white-space: nowrap;
  }
  .tagline::before { content: ""; flex: 0 0 68px; height: 2px; background: var(--ink-light); }
  .tagline::after { content: ""; flex: 1; height: 2px; background: var(--ink-light); }
</style>
</head>
<body>

<section class="card card-front" aria-label="Business card front">
  <svg class="shapes" viewBox="0 0 588 363" width="588" height="363" aria-hidden="true">
    <polygon fill="var(--band-navy)" points="0,165 397,165 381,188 0,188"/>
    <polygon fill="var(--brand-blue)" points="414,155 588,155 588,363 0,363 0,192 384,192"/>
  </svg>

  <div class="brand-lockup">
    <span class="brand-dot"></span>
    <span class="brand-name">Kestrel Office Clearance</span>
  </div>

  <ul class="contact-list">
    <li>07700 153928
      <svg viewBox="0 0 12 12"><rect x="2.5" y="0.5" width="7" height="11" rx="1.2" fill="none" stroke="#fff" stroke-width="1.2"/><rect x="4.5" y="9" width="3" height="1" fill="#fff"/></svg>
    </li>
    <li>01632 960418
      <svg viewBox="0 0 12 12"><path fill="#fff" d="M2.3 0.8l2 2.2-1.1 1.5c.8 1.7 2.2 3.1 3.9 3.9l1.5-1.1 2.2 2-1.3 1.9C5 11 1 7 .5 2.1z"/></svg>
    </li>
    <li>mark@kestrelofficeclearance.co.uk
      <svg viewBox="0 0 12 12"><rect x="0.5" y="2" width="11" height="8" fill="#fff"/><path d="M0.8 2.4L6 6.6l5.2-4.2" fill="none" stroke="var(--brand-blue)" stroke-width="1"/></svg>
    </li>
    <li>www.kestrelofficeclearance.co.uk
      <svg viewBox="0 0 12 12"><circle cx="6" cy="6" r="5.5" fill="#fff"/><path d="M3 3.5c1.5 0 2 1 1.5 2s.5 2 1.5 2.5M7.5 1.5c0 1.5 1 2 2.5 2" fill="none" stroke="var(--brand-blue)" stroke-width="1"/></svg>
    </li>
  </ul>

  <div class="person">
    <p class="person-name">Mark Holloway</p>
    <p class="person-role">Director</p>
    <p class="company-name">Kestrel Office Clearance</p>
    <address class="address">Unit K4 B, 2-8 Fenwick Lane<br>Harwick, Eastbury Vale<br>ZZ9 4QT</address>
  </div>
</section>

<section class="card card-back" aria-label="Business card back">
  <div class="back-lockup">
    <span class="back-dot"></span>
    <span class="back-name">Kestrel Office Clearance</span>
  </div>
  <p class="tagline">no-cost office clearing… simple, swift and tidy</p>
</section>

</body>
</html>
```